Very high end short term vacation rentals.

Coral Haven Coast Properties. Design business cards using existing logo. Should represent high quality, class accommodations. The back side will have a QR code linking to website/video and pictures

```html
<!DOCTYPE html>
<html lang="en">
<head>
<meta charset="utf-8">
<title>Coral Haven Coast Properties — Business Cards</title>
<link href="https://fonts.googleapis.com/css2?family=Cinzel:wght@400&family=Poppins:wght@400&display=swap" rel="stylesheet">
<style>
  :root {
    --page-bg: #e6e6e6;
    --card-white: #ffffff;
    --card-black: #000000;
    --ink: #111111;
    --ink-muted: #555555;
    --on-dark: #ffffff;
    --on-dark-soft: #e4e4e4;
    --divider: #8a8a8a;
  }
  * { margin: 0; padding: 0; box-sizing: border-box; }
  html, body {
    width: 1200px;
    height: 1085px;
    overflow: hidden;
    background: var(--page-bg);
  }
  .canvas {
    position: relative;
    width: 1200px;
    height: 1085px;
  }
  .card {
    position: absolute;
    left: 300px;
    width: 579px;
    height: 344px;
    overflow: hidden;
  }
  .card--front { top: 163px; background: var(--card-white); }
  .card--back { top: 542px; background: var(--card-black); }

  /* Front */
  .front-top {
    position: absolute;
    inset: 0 0 134px 0;
    background: var(--card-white);
  }
  .front-bottom {
    position: absolute;
    left: 0; right: 0; bottom: 0;
    height: 134px;
    background: var(--card-black);
  }
  .holder {
    position: absolute;
    right: 40px;
    top: 40px;
    text-align: right;
  }
  .holder__name {
    font-family: "Cinzel", serif;
    font-size: 25px;
    letter-spacing: 0.5px;
    color: var(--ink);
    line-height: 1.1;
  }
  .holder__title {
    font-family: "Poppins", sans-serif;
    font-size: 15.5px;
    color: var(--ink-muted);
    word-spacing: 3px;
    margin-top: 2px;
  }
  .brand-mark {
    position: absolute;
    left: 58px;
    top: 92px;
    width: 80px;
    height: 80px;
    border: 2px solid var(--ink);
    border-radius: 50%;
  }
  .brand-name {
    font-family: "Cinzel", serif;
    font-weight: 400;
    line-height: 1.05;
  }
  .brand-name--front {
    position: absolute;
    left: 136px;
    top: 138px;
    color: var(--ink);
  }
  .brand-name--front .brand-name__line1 { font-size: 26px; display: block; }
  .brand-name--front .brand-name__line2 { font-size: 20.5px; display: block; }

  .contact {
    position: absolute;
    left: 136px;
    top: 222px;
    font-family: "Poppins", sans-serif;
    color: var(--on-dark);
  }
  .contact__address { font-size: 16px; margin-bottom: 12px; }
  .contact__list { list-style: none; }
  .contact__item {
    display: flex;
    align-items: center;
    gap: 7px;
    font-size: 16px;
    line-height: 17px;
  }
  .contact__icon { width: 14px; height: 14px; flex: none; margin-left: 3px; }

  /* Back */
  .back-mark {
    position: absolute;
    left: 79px;
    top: 117px;
    width: 110px;
    height: 110px;
    border: 2px solid var(--on-dark);
    border-radius: 50%;
  }
  .back-divider {
    position: absolute;
    left: 209px;
    top: 118px;
    width: 1px;
    height: 109px;
    background: var(--divider);
  }
  .brand-name--back {
    position: absolute;
    left: 229px;
    top: 133px;
    color: var(--on-dark-soft);
  }
  .brand-name--back .brand-name__line1 { font-size: 31px; display: block; }
  .brand-name--back .brand-name__line2 { font-size: 24.5px; display: block; margin-top: 2px; }
</style>
</head>
<body>
<main class="canvas">

  <section class="card card--front" aria-label="Business card front">
    <div class="front-top"></div>
    <div class="front-bottom"></div>

    <div class="brand-mark"></div>
    <p class="brand-name brand-name--front">
      <span class="brand-name__line1">Coral Haven</span>
      <span class="brand-name__line2">Coast Properties</span>
    </p>

    <div class="holder">
      <p class="holder__name">ELIAS MARLOWE</p>
      <p class="holder__title">Managing Director</p>
    </div>

    <div class="contact">
      <p class="contact__address">123, 7th street, Country name, 123456</p>
      <ul class="contact__list">
        <li class="contact__item">
          <svg class="contact__icon" viewBox="0 0 24 24" aria-hidden="true"><path fill="#fff" d="M6.6 10.8c1.4 2.8 3.8 5.1 6.6 6.6l2.2-2.2c.3-.3.7-.4 1-.2 1.1.4 2.3.6 3.6.6.6 0 1 .4 1 1V20c0 .6-.4 1-1 1C10.6 21 3 13.4 3 4c0-.6.4-1 1-1h3.5c.6 0 1 .4 1 1 0 1.3.2 2.5.6 3.6.1.3 0 .7-.2 1z"/></svg>
          <span>044-123 456 789</span>
        </li>
        <li class="contact__item">
          <svg class="contact__icon" viewBox="0 0 24 24" aria-hidden="true"><path fill="#fff" d="M2 5h20v14H2z"/><path fill="none" stroke="#000" stroke-width="1.6" d="M2.5 5.5 12 13l9.5-7.5"/></svg>
          <span>info@email.com</span>
        </li>
        <li class="contact__item">
          <svg class="contact__icon" viewBox="0 0 24 24" aria-hidden="true"><g fill="none" stroke="#fff" stroke-width="1.8"><circle cx="12" cy="12" r="9.5"/><ellipse cx="12" cy="12" rx="4" ry="9.5"/><path d="M2.5 12h19M4 7h16M4 17h16"/></g></svg>
          <span>www.website.com</span>
        </li>
      </ul>
    </div>
  </section>

  <section class="card card--back" aria-label="Business card back">
    <div class="back-mark"></div>
    <div class="back-divider"></div>
    <p class="brand-name brand-name--back">
      <span class="brand-name__line1">Coral Haven</span>
      <span class="brand-name__line2">Coast Properties</span>
    </p>
  </section>

</main>
</body>
</html>
```